Book Cover Design RTM

Want a new book cover but want to use the same photo and change the sub name. This is for a brand called "Amber Meadow Living". The book is called "Quiet Steps, Bright Days"

This is for a 8.5 * 11 book size

We really want to brand the Amber Meadow Living

I've attached a sample of an old book cover, the photo I want used and the amber meadow living logo

Requirements
Must have
• Must have the logo,

must have the book title. "Quiet Steps, Bright Days"

Must have "Featuring" The Amber Meadow Living Tumble Card Game"

On the back put the logo and Amber Meadow Living Nutrition

must have the authors name "Norma Plaskett" on the page

"The Golden Stride Map"
Nice to have
• Amber Meadow Living Presents:

the book title

```html
<!DOCTYPE html>
<html lang="en">
<head>
<meta charset="utf-8">
<title>Quiet Steps, Bright Days — Book Cover</title>
<link rel="stylesheet" href="https://fonts.googleapis.com/css2?family=Anton&family=Michroma&family=Montserrat:wght@300;400;500;700&family=Oswald:wght@300;400&family=Archivo+Black&display=swap">
<style>
  :root {
    --backdrop: #e9e9ec;
    --cover: #000000;
    --ink: #ffffff;
    --accent: #62cdb4;
    --photo-top: #121816;
    --photo-mid: #1f3f38;
    --photo-low: #0e0e0e;
  }
  * { box-sizing: border-box; margin: 0; padding: 0; }
  html, body { width: 1200px; height: 900px; overflow: hidden; background: var(--backdrop); }
  .book {
    position: absolute; left: 55px; top: 31px;
    width: 1091px; height: 838px;
    background: var(--cover); color: var(--ink);
  }
  .back-cover { position: absolute; left: 0; top: 0; width: 530px; height: 838px; }
  .spine { position: absolute; left: 530px; top: 0; width: 33px; height: 838px; border-left: 1px solid #1a1a1a; border-right: 1px solid #1a1a1a; }
  .front-cover { position: absolute; left: 563px; top: 0; width: 528px; height: 838px; overflow: hidden; }

  /* back */
  .back-brand { position: absolute; left: 0; width: 530px; top: 262px; text-align: center; }
  .back-brand .mark-dot { display: block; width: 14px; height: 14px; border-radius: 50%; background: var(--ink); margin: 0 auto 26px; }
  .back-brand .brand-name { font-family: "Michroma", sans-serif; font-size: 22px; letter-spacing: 2px; }
  .back-brand .brand-line { font-family: "Michroma", sans-serif; font-size: 9px; letter-spacing: 3px; margin-top: 16px; }
  .back-blurb {
    position: absolute; left: 60px; top: 430px; width: 428px;
    font-family: "Oswald", sans-serif; font-weight: 300; font-size: 14.5px; line-height: 25.5px;
    text-transform: uppercase; text-align: justify;
  }
  .back-note {
    position: absolute; left: 60px; top: 690px; width: 270px;
    font-family: "Oswald", sans-serif; font-weight: 300; font-size: 14px; line-height: 25px;
    text-transform: uppercase;
  }

  /* vertical text helper: reads bottom to top */
  .vertical { position: absolute; writing-mode: vertical-rl; transform: rotate(180deg); white-space: nowrap; }

  .spine-brand { left: 6px; top: 36px; height: 170px; font-family: "Michroma", sans-serif; font-size: 8px; letter-spacing: 1px; line-height: 11px; text-align: end; }
  .spine-title { left: 8px; top: 266px; height: 360px; font-family: "Archivo Black", sans-serif; font-size: 15px; letter-spacing: 1.5px; text-align: center; }
  .spine-author { left: 9px; top: 650px; height: 122px; font-family: "Montserrat", sans-serif; font-weight: 400; font-size: 12px; letter-spacing: 1px; text-align: center; }

  /* front */
  .cover-photo {
    position: absolute; left: 200px; top: 0; width: 328px; height: 838px;
    background: linear-gradient(180deg, var(--photo-top) 0%, var(--photo-mid) 50%, var(--photo-low) 100%);
  }
  .front-brand-name { left: 18px; top: 47px; height: 370px; font-family: "Michroma", sans-serif; font-size: 21px; letter-spacing: 4px; line-height: 24px; text-align: start; }
  .front-brand-line { left: 46px; top: 47px; height: 370px; font-family: "Michroma", sans-serif; font-size: 9px; letter-spacing: 6px; line-height: 14px; text-align: start; }
  .front-title {
    left: 70px; top: 53px; height: 467px;
    font-family: "Anton", sans-serif; font-size: 60px; line-height: 63px; letter-spacing: 1px;
    text-transform: uppercase; text-align: start;
  }
  .tagline { position: absolute; left: 22px; top: 548px; width: 176px; font-family: "Montserrat", sans-serif; }
  .tagline .rule { height: 3px; background: var(--ink); }
  .tagline .line { font-weight: 500; font-size: 17px; line-height: 25px; letter-spacing: 0.5px; white-space: nowrap; }
  .tagline .accent { color: var(--accent); font-weight: 400; font-size: 20px; letter-spacing: 3px; }
  .tagline .accent.tight { letter-spacing: 0.5px; }
  .tagline .group { padding: 8px 0 6px; }
  .author { position: absolute; left: 22px; top: 758px; font-family: "Montserrat", sans-serif; font-weight: 300; font-size: 29px; letter-spacing: 0.5px; }
</style>
</head>
<body>
<div class="book">
  <section class="back-cover">
    <div class="back-brand">
      <span class="mark-dot"></span>
      <div class="brand-name">AMBER MEADOW LIVING</div>
      <div class="brand-line">NUTRITION</div>
    </div>
    <p class="back-blurb">Lorem ipsum dolor sit amet, consectetuer adipiscing elit, sed diam nonummy nibh euismod tincidunt ut laoreet dolore magna aliquam erat volutpat. Ut wisi enim ad minim veniam, quis nostrud exerci tation ullamcorper suscipit lobortis nisl ut aliquip ex ea commodo consequat. Duis autem vel eum iriure dolor in hendrerit in vulputate velit esse molestie consequat, vel illum dolore eu feugiat nulla facilisis at vero eros et accumsan et iusto odio dignissim qui blandit praesent luptatum zzril delenit augue duis dolore te feugait nulla facilisi.</p>
    <p class="back-note">Lorem ipsum dolor sit amet, consectetuer adipiscing elit, sed diam nonummy nibh euismod tincidunt ut laoreet dolore magna</p>
  </section>

  <section class="spine">
    <div class="vertical spine-brand">AMBER MEADOW<br>LIVING</div>
    <div class="vertical spine-title">QUIET STEPS BRIGHT DAYS</div>
    <div class="vertical spine-author">NORMA PLASKETT</div>
  </section>

  <section class="front-cover">
    <div class="cover-photo" role="img" aria-label="Photo of the author in workout wear with an exercise ball"></div>
    <div class="vertical front-brand-name">AMBER MEADOW</div>
    <div class="vertical front-brand-line">LIVING NUTRITION</div>
    <h1 class="vertical front-title">Quiet Steps<br>Bright Days</h1>
    <div class="tagline">
      <div class="rule"></div>
      <div class="group">
        <div class="line">The Golden Stride</div>
        <div class="line accent">MAP</div>
      </div>
      <div class="rule"></div>
      <div class="group">
        <div class="line">The Amber Meadow</div>
        <div class="line accent tight">LIVING TUMBLE</div>
        <div class="line">Card Game</div>
      </div>
      <div class="rule"></div>
    </div>
    <div class="author">NORMA PLASKETT</div>
  </section>
</div>
</body>
</html>
```